Best local air conditioning and heating contractor

We need a website design for a new company in Tampa Bay called the Coastal Breeze Cooling Company. We provide superior services for residential and commercial properties as well as maintenance and installing HVAC systems. We also want to sell equipment, parts and filter on the website as well. We want it easy to use for customers. Rich with content and keywords for our area.

Target Market(s)

homeowners in Tampa Bay

Industry/Entity Type

HVAC air conditioning and heating

Coding

Coded - Design and coding required

Number of Pages Required

5+ page

Font styles to use
Sans Serif

Requirements
Nice to have
• would like the colors to be same as logo

```html
<!DOCTYPE html>
<html lang="en">
<head>
<meta charset="utf-8">
<title>Coastal Breeze Cooling Company</title>
<link rel="stylesheet" href="https://fonts.googleapis.com/css2?family=Oswald:wght@300;400;500;600;700&family=Michroma&display=swap">
<style>
:root{
  --red:#d91f26;
  --red-dark:#b8161c;
  --navy:#1f2f6b;
  --navy-dark:#17245a;
  --text:#5b5f6b;
  --white:#ffffff;
  --line:#e4e6ec;
}
*{margin:0;padding:0;box-sizing:border-box}
html,body{width:1200px;height:3746px;overflow:hidden;background:var(--white)}
body{position:relative;font-family:'Oswald',sans-serif;color:var(--text)}
.abs{position:absolute}
.label{font-family:'Michroma',sans-serif;color:var(--red);font-size:15px;letter-spacing:2px;text-transform:uppercase;text-align:center;width:100%}
.heading{font-family:'Oswald',sans-serif;font-weight:600;color:var(--navy);font-size:52px;text-transform:uppercase;text-align:center;width:100%;letter-spacing:-.5px;line-height:1}
.btn{display:inline-flex;align-items:center;justify-content:space-between;width:max-content;white-space:nowrap;background:var(--red);color:var(--white);border-radius:24px;height:46px;padding:0 6px 0 22px;font-size:15px;text-transform:uppercase;font-weight:400;letter-spacing:-.2px}
.btn .dot{width:32px;height:32px;border-radius:50%;border:2px solid var(--white);display:flex;align-items:center;justify-content:center;margin-left:12px;flex:none}
.btn.center{left:50%;transform:translateX(-50%)}
.photo{position:absolute}
.brand{left:145px;top:26px;width:260px;font-weight:700;color:var(--navy);font-size:26px;line-height:1;text-transform:uppercase;display:flex;align-items:center;gap:10px;white-space:nowrap}
.brand .mark{width:34px;height:34px;border-radius:50%;background:var(--red);flex:none}
.topbar{left:608px;top:0;width:447px;height:41px;background:var(--red);color:var(--white);font-size:15px;display:flex;align-items:center;justify-content:center;gap:22px;white-space:nowrap}
.topbar-line{left:634px;top:48px;width:394px;height:4px;background:var(--red)}
.nav a{position:absolute;top:78px;font-size:15px;color:var(--navy);text-decoration:none;text-transform:uppercase}
.nav a.active{color:var(--red)}
.hero{left:0;top:112px;width:1200px;height:535px;background:linear-gradient(100deg,#3c3f45 0%,#5a5e66 35%,#8d9096 60%,#6d6f72 100%)}
.hero-title{left:144px;top:248px;text-transform:uppercase;font-weight:600;line-height:1;white-space:nowrap}
.hero-title .l1{font-size:50px;color:var(--red);letter-spacing:1px}
.hero-title .l2{font-size:56px;color:var(--white);margin-top:6px}
.dots span{position:absolute;left:1124px;width:12px;height:12px;border-radius:50%;background:var(--white)}
.about-text{left:169px;top:900px;width:862px;text-align:center;font-size:15.5px;line-height:27px;font-weight:300;color:#5b5f6b}
.frame{border:3px solid var(--red)}
.card{position:absolute;display:flex;align-items:flex-end;justify-content:center;padding-bottom:30px;color:var(--white);font-size:21px;font-weight:600;text-transform:uppercase;white-space:nowrap}
.product{position:absolute;background:var(--white);box-shadow:0 6px 30px rgba(20,30,70,.08)}
.product .img{position:absolute;left:17px;top:24px;width:142px;height:205px}
.product .name{position:absolute;left:176px;top:24px;font-size:21px;font-weight:500;color:var(--navy);text-transform:uppercase;white-space:nowrap}
.product .price{position:absolute;left:176px;top:65px;font-size:20px;font-weight:300;color:var(--red);white-space:nowrap}
.product .price span{color:#f0a020;font-size:15px;margin-left:14px;letter-spacing:1px}
.product .desc{position:absolute;left:176px;top:104px;width:240px;font-size:15px;line-height:26px;font-weight:300}
.product .btn{position:absolute;left:176px;top:175px}
.arrow{position:absolute;top:2735px;width:44px;height:44px;border-radius:50%;border:1.5px solid #555;display:flex;align-items:center;justify-content:center}
.field{position:absolute;left:777px;width:238px;height:36px;background:var(--white);font-size:13px;color:#666;padding:10px 24px;font-weight:300}
.fcol h4{position:absolute;font-size:21px;font-weight:500;color:var(--navy);text-transform:uppercase}
.ftext{position:absolute;font-size:13px;font-weight:300;color:#555;line-height:20px}
.social{position:absolute;top:3672px;width:30px;height:30px;border-radius:50%;border:2px solid}
</style>
</head>
<body>

<div class="abs brand"><span class="mark"></span><span>Coastal Breeze<br>Cooling Co.</span></div>
<div class="abs topbar">
  <span style="display:flex;align-items:center;gap:6px"><svg width="14" height="14" viewBox="0 0 24 24"><path fill="#fff" d="M6.6 10.8a15 15 0 0 0 6.6 6.6l2.2-2.2a1 1 0 0 1 1-.25 11.4 11.4 0 0 0 3.6.57 1 1 0 0 1 1 1V20a1 1 0 0 1-1 1A17 17 0 0 1 3 4a1 1 0 0 1 1-1h3.5a1 1 0 0 1 1 1c0 1.25.2 2.45.57 3.57a1 1 0 0 1-.25 1z"/></svg>+1 555 010 0199</span>
  <span style="display:flex;align-items:center;gap:6px"><svg width="15" height="12" viewBox="0 0 20 16"><path fill="#fff" d="M0 0h20v16H0z"/><path fill="none" stroke="#d91f26" stroke-width="2" d="M1 1l9 7 9-7"/></svg>hello@coastalbreezecooling.com</span>
</div>
<div class="abs topbar-line"></div>
<nav class="nav">
  <a class="active" style="left:607px">Home</a>
  <a style="left:681px">About</a>
  <a style="left:761px">Services</a>
  <a style="left:856px">Shop</a>
  <a style="left:929px">News</a>
  <a style="left:1003px">Contact</a>
</nav>

<div class="photo hero" role="img" aria-label="HVAC technician in hard hat servicing a rooftop air conditioning unit above a city"></div>
<div class="abs hero-title"><div class="l1">Coastal Breeze</div><div class="l2">Cooling Company</div></div>
<div class="abs btn" style="left:144px;top:390px">Get Started<span class="dot"><svg width="14" height="14" viewBox="0 0 24 24"><path d="M5 12h13M13 6l6 6-6 6" fill="none" stroke="#fff" stroke-width="2.5"/></svg></span></div>
<div class="dots"><span style="top:317px"></span><span style="top:342px;background:var(--red)"></span><span style="top:365px"></span></div>
<svg class="abs" style="left:0;top:560px" width="1200" height="90" viewBox="0 0 1200 90">
  <path d="M0 90 L0 72 L270 20 L600 66 L870 18 L1200 72 L1200 90 Z" fill="#fff"/>
  <path d="M60 70 L270 24 L500 56" fill="none" stroke="var(--red)" stroke-width="6"/>
  <path d="M680 56 L870 22 L1100 70" fill="none" stroke="var(--red)" stroke-width="6"/>
  <path d="M150 62 L270 34 L420 55" fill="none" stroke="var(--navy)" stroke-width="3"/>
  <path d="M760 55 L870 32 L1010 62" fill="none" stroke="var(--navy)" stroke-width="3"/>
</svg>

<div class="abs label" style="top:786px">About</div>
<div class="abs heading" style="top:818px">Who We Are</div>
<p class="abs about-text">Sed ut perspiciatis unde omnis iste natus error sit voluptatem accusantium doloremque laudantium, totam rem aperiam, eaque ipsa quae ab illo inventore veritatis et quasi architecto beatae vitae dicta sunt explicabo. Nemo enim ipsam voluptatem quia voluptas sit aspernatur aut odit aut fugit, sed quia consequuntur magni dolores eos qui ratione voluptatem sequi nesciunt. Neque porro quisquam est, qui dolorem ipsum quia dolor sit amet, consectetur, adipisci velit, sed quia non numquam eius modi tempora incidumagnarum exercitationem ullam corporis suscipit laboriosam, nisi ut aliquid ex ea commodi</p>
<div class="abs btn center" style="top:1035px">Read More<span class="dot"><svg width="14" height="14" viewBox="0 0 24 24"><path d="M5 12h13M13 6l6 6-6 6" fill="none" stroke="#fff" stroke-width="2.5"/></svg></span></div>

<svg class="abs" style="left:0;top:1255px" width="1200" height="960" viewBox="0 0 1200 960">
  <path d="M0 214 L1200 6 L1200 960 L0 960 Z" fill="var(--navy)"/>
  <path d="M0 121 L225 178 L0 214 Z" fill="var(--red)"/>
</svg>
<div class="abs frame" style="left:873px;top:1087px;width:150px;height:160px"></div>
<div class="abs frame" style="left:186px;top:1373px;width:151px;height:160px"></div>
<div class="photo" style="left:225px;top:1124px;width:751px;height:381px;background:linear-gradient(110deg,#8a97a8 0%,#5d7090 35%,#9aa0a6 60%,#4c4f55 100%)" role="img" aria-label="Technician in cap checking gauges on an outdoor AC condenser"></div>
<svg class="abs" style="left:576px;top:1290px" width="48" height="48" viewBox="0 0 48 48"><circle cx="24" cy="24" r="24" fill="var(--red)"/><path d="M19 14 L34 24 L19 34 Z" fill="#fff"/></svg>

<div class="abs label" style="top:1578px">Services</div>
<div class="abs heading" style="top:1609px;color:var(--white)">What We Do</div>
<div class="card" style="left:0;top:1718px;width:288px;height:343px;background:linear-gradient(180deg,#c9ced6 0%,#7c8694 55%,#1d2230 100%)" role="img" aria-label="Residential AC condenser unit">Residential</div>
<div class="card" style="left:297px;top:1702px;width:298px;height:343px;background:linear-gradient(180deg,#c8a0aa 0%,#e0606a 55%,#d91f26 100%)" role="img" aria-label="Commercial cooling unit under steel structure">Commercial</div>
<div class="card" style="left:604px;top:1718px;width:299px;height:343px;background:linear-gradient(180deg,#8a8660 0%,#6a6450 50%,#1d1d22 100%)" role="img" aria-label="Technician wiring an HVAC system">Installing HVAC Systems</div>
<div class="card" style="left:912px;top:1702px;width:288px;height:343px;background:linear-gradient(180deg,#3f73b8 0%,#a9b4c2 50%,#2a2f3a 100%)" role="img" aria-label="Rooftop HVAC units under blue sky">Maintenance</div>
<div class="abs btn center" style="top:2096px">View More Services<span class="dot"><svg width="14" height="14" viewBox="0 0 24 24"><path d="M5 12h13M13 6l6 6-6 6" fill="none" stroke="#fff" stroke-width="2.5"/></svg></span></div>

<div class="abs label" style="top:2297px">Shop</div>
<div class="abs heading" style="top:2326px">Featured Products</div>

<div class="product" style="left:-80px;top:2452px;width:447px;height:253px">
  <div class="img photo" style="left:38px;background:linear-gradient(135deg,#f2f2f2,#c6c9ce)" role="img" aria-label="Metal HVAC mounting rails"></div>
  <div class="name" style="left:185px">Product Name</div>
  <div class="price" style="left:185px">$57.23<span>★★★★★</span></div>
  <div class="desc" style="left:185px">Sed ut perspiciatis unde omnis iste natus error sit voluptatem accusantium</div>
  <div class="btn" style="left:185px">View Product<span class="dot"><svg width="14" height="14" viewBox="0 0 24 24"><path d="M5 12h13M13 6l6 6-6 6" fill="none" stroke="#fff" stroke-width="2.5"/></svg></span></div>
</div>
<div class="product" style="left:381px;top:2428px;width:438px;height:253px">
  <div class="img photo" style="background:linear-gradient(135deg,#f4f4f4,#b9cfc6)" role="img" aria-label="Green coiled refrigerant hose"></div>
  <div class="name">Product Name</div>
  <div class="price">$57.23<span>★★★★★</span></div>
  <div class="desc">Sed ut perspiciatis unde omnis iste natus error sit voluptatem accusantium</div>
  <div class="btn">View Product<span class="dot"><svg width="14" height="14" viewBox="0 0 24 24"><path d="M5 12h13M13 6l6 6-6 6" fill="none" stroke="#fff" stroke-width="2.5"/></svg></span></div>
</div>
<div class="product" style="left:833px;top:2452px;width:447px;height:253px">
  <div class="img photo" style="background:linear-gradient(135deg,#f6f6f6,#d6d8dc)" role="img" aria-label="White portable air conditioner"></div>
  <div class="name">Product Name</div>
  <div class="price">$57.23<span>★★★★★</span></div>
  <div class="desc">Sed ut perspiciatis unde omnis iste natus error sit voluptatem accusantium</div>
  <div class="btn">View Product<span class="dot"><svg width="14" height="14" viewBox="0 0 24 24"><path d="M5 12h13M13 6l6 6-6 6" fill="none" stroke="#fff" stroke-width="2.5"/></svg></span></div>
</div>
<div class="arrow" style="left:553px"><svg width="14" height="14" viewBox="0 0 24 24"><path d="M16 3 L7 12 L16 21" fill="none" stroke="#333" stroke-width="2.5"/></svg></div>
<div class="arrow" style="left:602px"><svg width="14" height="14" viewBox="0 0 24 24"><path d="M8 3 L17 12 L8 21" fill="none" stroke="#333" stroke-width="2.5"/></svg></div>

<svg class="abs" style="left:0;top:2790px" width="1200" height="690" viewBox="0 0 1200 690">
  <defs>
    <linearGradient id="sky" x1="0" y1="0" x2="0" y2="1">
      <stop offset="0" stop-color="#5d5a78"/><stop offset=".45" stop-color="#b58a9c"/><stop offset=".75" stop-color="#a45a6a"/><stop offset="1" stop-color="#7a3a4a"/>
    </linearGradient>
    <linearGradient id="redfade" x1="0" y1="0" x2="1" y2="0">
      <stop offset="0" stop-color="#d91f26" stop-opacity=".92"/><stop offset="1" stop-color="#d91f26" stop-opacity=".75"/>
    </linearGradient>
  </defs>
  <path d="M0 2 L1200 58 L1200 530 L0 680 Z" fill="url(#sky)" role="img" aria-label="City skyline along a river at dusk"/>
  <path d="M836 60 L1200 4 L1200 40 Z" fill="var(--navy)"/>
  <path d="M0 440 L740 250 L740 560 L0 680 Z" fill="url(#redfade)"/>
</svg>
<div class="abs label" style="left:134px;top:3262px;width:auto;text-align:left;color:#fff">Contact</div>
<div class="abs" style="left:134px;top:3288px;font-size:55px;font-weight:600;color:#fff;text-transform:uppercase;line-height:1;white-space:nowrap">Request A Call Back</div>
<svg class="abs" style="left:737px;top:2899px" width="318" height="460" viewBox="0 0 318 460"><path d="M0 61 L318 0 L318 460 L0 460 Z" fill="var(--red)"/></svg>
<div class="abs" style="left:737px;top:2975px;width:318px;text-align:center;font-size:58px;font-weight:600;color:#fff;text-transform:uppercase;line-height:1">Contact</div>
<div class="field" style="top:3062px">Enter Name</div>
<div class="field" style="top:3107px">Enter Email</div>
<div class="field" style="top:3152px">Enter Phone</div>
<div class="field" style="top:3197px;height:79px">Message</div>
<div class="abs btn" style="left:777px;top:3286px;background:var(--navy)">Submit<span class="dot"><svg width="14" height="14" viewBox="0 0 24 24"><path d="M5 12h13M13 6l6 6-6 6" fill="none" stroke="#fff" stroke-width="2.5"/></svg></span></div>

<div class="abs brand" style="left:175px;top:3490px;width:300px;font-size:30px"><span class="mark" style="width:40px;height:40px"></span><span>Coastal Breeze<br>Cooling Co.</span></div>
<div class="abs" style="left:549px;top:3447px;width:3px;height:131px;background:var(--red)"></div>
<div class="fcol"><h4 style="left:570px;top:3458px">Contact</h4></div>
<svg class="abs" style="left:570px;top:3503px" width="14" height="12" viewBox="0 0 14 12"><path d="M0 2 L4 0 L9 2 L14 0 L14 10 L9 12 L4 10 L0 12 Z" fill="var(--red)"/></svg>
<div class="ftext" style="left:596px;top:3498px">2134, perspiciatis unde omnis iste<br>natus error sit volcusantium</div>
<svg class="abs" style="left:570px;top:3555px" width="13" height="13" viewBox="0 0 24 24"><path fill="var(--red)" d="M6.6 10.8a15 15 0 0 0 6.6 6.6l2.2-2.2a1 1 0 0 1 1-.25 11.4 11.4 0 0 0 3.6.57 1 1 0 0 1 1 1V20a1 1 0 0 1-1 1A17 17 0 0 1 3 4a1 1 0 0 1 1-1h3.5a1 1 0 0 1 1 1c0 1.25.2 2.45.57 3.57a1 1 0 0 1-.25 1z"/></svg>
<div class="ftext" style="left:596px;top:3552px">+1 555 010 0199</div>
<div class="abs" style="left:853px;top:3447px;width:3px;height:131px;background:var(--red)"></div>
<div class="fcol"><h4 style="left:874px;top:3458px">Menus</h4></div>
<div class="ftext" style="left:900px;top:3498px">Home<br>About Us<br>Services</div>
<div class="ftext" style="left:988px;top:3498px">Shop<br>News<br>Contact</div>
<div class="abs" style="left:0;top:3641px;width:1200px;height:1px;background:var(--line)"></div>
<div class="social" style="left:175px;border-color:#3b5bb5"></div>
<div class="social" style="left:213px;border-color:#b03a8a"></div>
<div class="social" style="left:251px;border-color:var(--red)"></div>
<div class="ftext" style="left:560px;top:3677px;width:482px;text-align:right;white-space:nowrap">© 2024 Coastal Breeze Cooling Company. All rights reserved Privacy &nbsp;|&nbsp; Terms of Use</div>

</body>
</html>
```